Heron Loan Partners Business Card

We need a business card design for our mortgage servicing company. In addition to servicing the loans of homeowners, we help homeowners with purchasing their homes and any mortgage refinancing. We would like to see designs that use the colors in the logo attached below (gold-ish yellow and navy blue), and any other design you deem fit! The design should communicate a simpler life with smart mortgages provided by Heron.

```html
<!DOCTYPE html>
<html lang="en">
<head>
<meta charset="utf-8">
<title>Heron Loan Partners – Business Card</title>
<link rel="stylesheet" href="https://fonts.googleapis.com/css2?family=Montserrat:wght@600;700&family=Open+Sans:wght@400;600&display=swap">
<style>
  :root {
    --navy: #2a1f57;
    --gold: #e0b03c;
    --ink: #111111;
    --paper: #ffffff;
    --backdrop: #e9e8ec;
    --rule: #222222;
  }
  * { box-sizing: border-box; margin: 0; padding: 0; }
  html, body { width: 1200px; height: 780px; overflow: hidden; }
  body {
    background: var(--backdrop);
    display: flex;
    align-items: center;
    justify-content: center;
    gap: 40px;
    font-family: "Open Sans", Arial, sans-serif;
  }
  .card {
    width: 540px;
    height: 310px;
    position: relative;
    overflow: hidden;
    box-shadow: 0 10px 30px rgba(0,0,0,0.18);
  }
  .card--back {
    background: var(--navy);
    display: flex;
    align-items: center;
    justify-content: center;
  }
  .brand {
    font-family: "Montserrat", Arial, sans-serif;
    font-weight: 700;
    color: var(--gold);
    letter-spacing: 0.5px;
  }
  .card--back .brand { font-size: 40px; }
  .card--front { background: var(--paper); }
  .card--front .brand {
    position: absolute;
    top: 62px;
    left: 0;
    right: 0;
    text-align: center;
    font-size: 30px;
  }
  .person {
    position: absolute;
    left: 58px;
    top: 168px;
  }
  .person__name {
    font-family: "Montserrat", Arial, sans-serif;
    font-weight: 700;
    font-size: 25px;
    color: var(--ink);
    white-space: nowrap;
  }
  .person__first { color: var(--gold); }
  .person__role {
    font-size: 14px;
    color: var(--ink);
    margin-top: 2px;
    padding-left: 50px;
  }
  .divider {
    position: absolute;
    left: 300px;
    top: 150px;
    width: 1px;
    height: 72px;
    background: var(--rule);
  }
  .contact {
    position: absolute;
    left: 322px;
    top: 148px;
    list-style: none;
    font-size: 13px;
    color: var(--ink);
  }
  .contact li {
    display: flex;
    align-items: center;
    gap: 8px;
    height: 24px;
  }
  .contact svg { width: 13px; height: 13px; flex: none; }
  .address-band {
    position: absolute;
    left: 0;
    right: 0;
    bottom: 14px;
    height: 34px;
    background: var(--gold);
    color: var(--paper);
    font-size: 14px;
    font-weight: 600;
    display: flex;
    align-items: center;
    justify-content: center;
    letter-spacing: 0.3px;
  }
</style>
</head>
<body>
  <section class="card card--back">
    <div class="brand">Heron Loan Partners</div>
  </section>

  <section class="card card--front">
    <div class="brand">Heron Loan Partners</div>

    <div class="person">
      <div class="person__name"><span class="person__first">Lucia</span> Varenka</div>
      <div class="person__role">Managing Director</div>
    </div>

    <div class="divider"></div>

    <ul class="contact">
      <li>
        <svg viewBox="0 0 16 16" aria-hidden="true"><path fill="var(--gold)" d="M3.6 1.5l2.3 2.3-1.4 1.9c.9 2 2.7 3.8 4.7 4.7l1.9-1.4 2.3 2.3-1.6 2.2C6.7 14.8 1.2 9.3 1.4 3.1z"/></svg>
        (555) 214-3086
      </li>
      <li>
        <svg viewBox="0 0 16 16" aria-hidden="true"><rect x="1" y="3" width="14" height="10" rx="1" fill="var(--gold)"/><path d="M1.5 3.8L8 9l6.5-5.2" stroke="#fff" stroke-width="1.4" fill="none"/></svg>
        hello@heronloans.example
      </li>
      <li>
        <svg viewBox="0 0 16 16" aria-hidden="true"><circle cx="8" cy="8" r="7" fill="var(--gold)"/><path d="M1 8h14M8 1c-3 3.5-3 10.5 0 14M8 1c3 3.5 3 10.5 0 14" stroke="#fff" stroke-width="1" fill="none"/></svg>
        www.heronloans.example
      </li>
    </ul>

    <div class="address-band">2187 Calloway Ct #204, Ashford, FL 32019, USA</div>
  </section>
</body>
</html>
```